Homemaking training schools needs a Business Card design

Designer, Hello!

No special requirements, good-looking enough.
--------------------------------------------------------------------------

Name: Marcus Dole
Chairman
Tel: 0574-71948263
Mobile: 13857420916
Email: kelvora@mailnest.example
Web: www.prt2019.example
Add: No.258, LanpingJie, BeiyuanQu, Ningbo, Zhejiang

LOGO
Ningbo PRT Homemaking Training School

Target Market(s)

pregnant women, mothers, infants, the elderly and families, including cleaning, cooking, nursing training.

Industry/Entity Type

Business

Contact Information for Business Card

Name: Marcus Dole
Chairman
Tel: 0574-71948263
Mobile: 13857420916
Email: kelvora@mailnest.example
Web: www.prt2019.example

LOGO

Font styles to use
Serif
Sans Serif
Decorative

Requirements
Nice to have
• Feels: clean, specifications, safety, comfort, warmth and happiness.

```html
<!DOCTYPE html>
<html lang="en">
<head>
<meta charset="utf-8">
<title>PingRuiTang Business Card</title>
<link rel="stylesheet" href="https://fonts.googleapis.com/css2?family=Montserrat:wght@400;600;700&family=Nunito:wght@800&display=swap">
<style>
  :root {
    --blue: #1a73c0;
    --pink: #e8197f;
    --grey: #6b6b6b;
    --ink: #2a2a2a;
    --card: #ffffff;
    --bg: #2b2b2d;
  }
  * { box-sizing: border-box; margin: 0; padding: 0; }
  html, body { width: 1200px; height: 900px; overflow: hidden; }
  body {
    background: var(--bg);
    font-family: "Montserrat", Arial, sans-serif;
    position: relative;
  }
  .card {
    position: absolute;
    left: 285px;
    width: 630px;
    height: 360px;
    background: var(--card);
    box-shadow: 0 10px 28px rgba(0,0,0,.45);
    overflow: hidden;
  }
  .card--front { top: 60px; }
  .card--back { top: 480px; }

  .brand { position: absolute; text-align: center; }
  .brand__row { display: flex; align-items: center; justify-content: center; gap: 8px; }
  .brand__dot { width: 16px; height: 16px; border-radius: 50%; background: var(--pink); }
  .brand__name {
    font-family: "Nunito", "Montserrat", sans-serif;
    font-weight: 800;
    color: var(--blue);
    letter-spacing: .5px;
    line-height: 1;
  }
  .brand__tagline {
    display: flex; align-items: center; gap: 10px;
    color: var(--grey); font-weight: 400;
    margin-top: 6px;
  }
  .brand__tagline::before, .brand__tagline::after {
    content: ""; flex: 1; height: 1px; background: var(--grey);
  }

  .card--front .brand { left: 0; right: 0; top: 120px; }
  .card--front .brand__name { font-size: 44px; }
  .card--front .brand__tagline { width: 380px; margin: 8px auto 0; font-size: 17px; }
  .card--front .brand__web {
    margin-top: 10px; color: var(--blue); font-weight: 700; font-size: 15px;
  }

  .card--back .brand { left: 40px; top: 70px; width: 320px; }
  .card--back .brand__name { font-size: 36px; }
  .card--back .brand__tagline { font-size: 14px; }

  .divider {
    position: absolute; left: 0; right: 0; top: 205px;
    height: 2px; background: var(--blue);
  }
  .person { position: absolute; right: 36px; top: 150px; width: 230px; }
  .person__name {
    color: var(--blue); font-weight: 700; font-size: 22px; letter-spacing: .5px;
  }
  .person__title {
    color: var(--ink); font-weight: 700; font-size: 11px; letter-spacing: 1px; margin-top: 2px;
  }
  .contacts { position: absolute; right: 36px; top: 218px; width: 230px; list-style: none; }
  .contacts__item {
    display: flex; align-items: center; gap: 8px;
    color: var(--blue); font-weight: 600; font-size: 13px; line-height: 21px;
  }
  .contacts__icon { width: 11px; height: 11px; flex: none; }
  .address {
    position: absolute; left: 40px; bottom: 34px;
    color: var(--blue); font-weight: 600; font-size: 13px; line-height: 19px;
    font-style: normal;
  }
</style>
</head>
<body>

<section class="card card--front">
  <div class="brand">
    <div class="brand__row">
      <span class="brand__dot"></span>
      <span class="brand__name">PingRuiTang</span>
    </div>
    <div class="brand__tagline">Training &amp; Services</div>
    <div class="brand__web">www.prt2019.example</div>
  </div>
</section>

<section class="card card--back">
  <div class="brand">
    <div class="brand__row">
      <span class="brand__dot"></span>
      <span class="brand__name">PingRuiTang</span>
    </div>
    <div class="brand__tagline">Training &amp; Services</div>
  </div>

  <div class="person">
    <div class="person__name">MARCUS DOLE</div>
    <div class="person__title">CHAIRMAN</div>
  </div>
  <div class="divider"></div>

  <ul class="contacts">
    <li class="contacts__item">
      <svg class="contacts__icon" viewBox="0 0 12 12"><path d="M2.5 1l2 2.2-1 1.3c.7 1.5 1.8 2.6 3.2 3.3l1.3-1 2.2 2-1 1.7C5.7 10.3 1.7 6.4 1 2z" fill="#2a2a2a"/></svg>
      0574-71948263
    </li>
    <li class="contacts__item">
      <svg class="contacts__icon" viewBox="0 0 12 12"><rect x="3" y="0.8" width="6" height="10.4" rx="1" fill="none" stroke="#2a2a2a" stroke-width="1.2"/><circle cx="6" cy="9.3" r=".7" fill="#2a2a2a"/></svg>
      13857420916
    </li>
    <li class="contacts__item">
      <svg class="contacts__icon" viewBox="0 0 12 12"><rect x="0.8" y="2.5" width="10.4" height="7" fill="none" stroke="#2a2a2a" stroke-width="1.1"/><path d="M1 3l5 3.6L11 3" fill="none" stroke="#2a2a2a" stroke-width="1.1"/></svg>
      kelvora@mailnest.example
    </li>
    <li class="contacts__item">
      <svg class="contacts__icon" viewBox="0 0 12 12"><circle cx="6" cy="6" r="5" fill="none" stroke="#2a2a2a" stroke-width="1.1"/><ellipse cx="6" cy="6" rx="2.2" ry="5" fill="none" stroke="#2a2a2a" stroke-width="1"/><path d="M1 6h10" stroke="#2a2a2a" stroke-width="1"/></svg>
      www.prt2019.example
    </li>
  </ul>

  <address class="address">
    258, LanpingJie<br>
    BeiyuanQu, Ningbo, Zhejiang
  </address>
</section>

</body>
</html>
```